QuillVane needs a dashboard page designed

Redesign the dashboard shown in the provided images.

There are two images:
- dashboard.png
- dashboard-expanded.png

NOTE: The vocabulary navigation on the left will be a very long list of words 100s, so keep that in mind when you're designing both the vocab navigation and the expanded vocab popup.

In the dashboard.png picture, there needs to be a progress chart showing the word progress like the following: review 1(show it as completed) -> review 2(show the user they are here) -> review 3(unvisited) -> review 4(unvisited)

The do-not-design-this-page.png image is for your reference only. It is not to be designed. Use it to understand the overall look and feel of the website to help you create the best dashboard page possible.
Updates

Need extra days to review

Industry/Entity Type

Education English learning

Number of Pages Required

1 page

Requirements
Must have
• The main navigation and main header cannot change between pages. See the do-not-design page for the main navigateion and header.
Should not have
• Do not add a person profile. We will not have images of our users. Keep the icons in the main navigation as they are.

```html
<!DOCTYPE html>
<html lang="en">
<head>
<meta charset="utf-8">
<title>QuillVane Dashboard</title>
<link href="https://fonts.googleapis.com/css2?family=Poppins:wght@300;400;500;600&display=swap" rel="stylesheet">
<style>
:root{
  --stage:#2f2f2f;
  --navy:#0f2f4f;
  --navy-deep:#0b2744;
  --slate:#4e6479;
  --charcoal:#2b3440;
  --ink:#1d2b3a;
  --text:#3a4654;
  --muted:#6b7480;
  --page:#eef4fb;
  --white:#ffffff;
  --line:#d6dee8;
  --chip:#e8f1fb;
  --step-off:#b7c1cc;
  --close:#d62828;
}
*{box-sizing:border-box;margin:0;padding:0}
html,body{width:1200px;height:509px;overflow:hidden;background:var(--stage);font-family:"Poppins",sans-serif}
.screen{position:absolute;top:60.6px;width:531px;height:387.5px;overflow:hidden;background:linear-gradient(160deg,#f3f8fd,#eaf2fb);}
.screen--main{left:56.4px}
.screen--modal{left:612.5px}
.abs{position:absolute;line-height:1;white-space:nowrap}
.sidebar{position:absolute;left:0;top:0;width:113px;height:100%;background:var(--navy-deep);color:#e6edf5}
.brand{left:17px;top:12px;font-size:13.6px;font-weight:400;color:#fff}
.nav-group{font-size:5.6px;font-weight:500;text-transform:uppercase;display:flex;align-items:center;gap:2.5px;color:#fff}
.nav-item{font-size:5.4px;font-weight:400;color:#dbe4ee}
.pill{position:absolute;background:#1e3d5e;color:#fff;font-size:4.2px;border-radius:2px;display:flex;align-items:center;justify-content:center;gap:1.5px}
.pill--dark{background:var(--navy-deep)}
.topbar{position:absolute;left:113px;top:0;right:0;height:32.6px;border-bottom:0.5px solid var(--line)}
.search{position:absolute;left:328px;top:10.7px;width:72px;height:13.3px;background:#fff;border-radius:6px;font-size:5px;color:var(--muted);display:flex;align-items:center;justify-content:space-between;padding:0 5px}
.avatar{position:absolute;left:311px;top:11.5px;width:11px;height:11px;border-radius:50%;background:linear-gradient(135deg,#e7b08a,#7a4a33)}
.crumb{font-size:8.4px;font-weight:500;color:var(--navy)}
.crumb-leaf{font-size:5.8px;color:var(--ink)}
.subtitle{font-size:7px;color:var(--ink)}
.section-title{font-size:8px;font-weight:500;color:var(--navy)}
.step{position:absolute;width:10px;height:10px;border-radius:50%;color:#fff;font-size:5px;display:flex;align-items:center;justify-content:center}
.step--done,.step--current{background:var(--navy)}
.step--todo{background:var(--step-off)}
.step-label{font-size:5.4px;color:var(--ink)}
.step-line{position:absolute;top:105px;height:0.5px;background:var(--line)}
.card{position:absolute;top:125.8px;width:119px;height:31.2px;border-radius:2.5px;color:#fff;padding:6px 10.5px}
.card h3{font-size:8px;font-weight:500;line-height:1}
.card p{font-size:5.8px;margin-top:4px;line-height:1}
.card--due{background:var(--navy)}
.card--working{background:var(--slate)}
.card--long{background:var(--charcoal)}
.body-copy{position:absolute;left:130px;width:383px;font-size:4.85px;line-height:8px;color:var(--text);white-space:normal}
.chart{position:absolute;left:129.5px;top:207px;width:384px;height:106.5px;background:#fff;border-radius:3px}
.analysis-title{font-size:6.4px;color:var(--ink)}
.veil{position:absolute;inset:0;background:rgba(255,255,255,0.8)}
.sidebar-veil{position:absolute;left:0;top:0;width:113px;height:100%;background:rgba(190,202,214,0.72)}
.vocab-popup{position:absolute;left:94px;top:57.3px;width:406.6px;height:150px;background:#fff;border-radius:3px;box-shadow:0 2px 10px rgba(15,47,79,0.12)}
.vocab-popup::before{content:"";position:absolute;inset:3.5px;border:0.5px solid var(--line);border-radius:2px}
.close{position:absolute;left:390.5px;top:8.6px;width:8px;height:8px;border-radius:50%;background:var(--close)}
.chip{position:absolute;left:9.3px;width:79px;height:15px;background:var(--chip);border-radius:2px;font-size:5.6px;font-weight:500;color:var(--ink);display:flex;align-items:center;padding-left:12.5px}
.word{font-size:5.6px;font-weight:500;color:var(--ink)}
</style>
</head>
<body>

<!-- Dashboard -->
<section class="screen screen--main">
  <aside class="sidebar">
    <div class="abs brand">QuillVane</div>
    <div class="abs nav-group" style="left:17px;top:42.8px">
      <svg width="5" height="5" viewBox="0 0 10 10"><path d="M5 1 L10 5.5 H8.5 V9.5 H6 V7 H4 V9.5 H1.5 V5.5 H0 Z" fill="#fff"/></svg>Word Coach
      <svg width="4" height="4" viewBox="0 0 10 10"><path d="M2 3.5 L5 6.5 L8 3.5" stroke="#fff" stroke-width="1.5" fill="none"/></svg>
    </div>
    <div class="pill" style="left:92px;top:42px;width:15px;height:8.4px">All<svg width="3" height="3" viewBox="0 0 10 10"><path d="M2 3.5 L5 6.5 L8 3.5" stroke="#fff" stroke-width="1.5" fill="none"/></svg></div>
    <div class="abs nav-item" style="left:17px;top:63.5px">Short Term Memory</div>
    <div class="abs nav-item" style="left:17px;top:73.8px;display:flex;align-items:center;gap:3.5px">
      <svg width="5" height="5" viewBox="0 0 10 10"><circle cx="5" cy="5" r="4" stroke="#dbe4ee" fill="none"/><circle cx="5" cy="5" r="1.8" fill="#dbe4ee"/></svg>Grab</div>
    <div class="abs nav-item" style="left:17px;top:92.8px">Working Memory</div>
    <div class="abs nav-item" style="left:17px;top:111px">Long term Memory</div>
    <div class="abs nav-group" style="left:17px;top:134.8px">
      <svg width="6" height="5" viewBox="0 0 12 10"><path d="M1 1.5 L4 0.5 L8 1.5 L11 0.5 V8.5 L8 9.5 L4 8.5 L1 9.5 Z M4 0.5 V8.5 M8 1.5 V9.5" stroke="#fff" fill="none"/></svg>Daily English
      <svg width="4" height="4" viewBox="0 0 10 10"><path d="M2 3.5 L5 6.5 L8 3.5" stroke="#fff" stroke-width="1.5" fill="none"/></svg>
    </div>
    <div class="abs nav-group" style="left:17px;top:159px">
      <svg width="4.5" height="5.5" viewBox="0 0 8 10"><rect x="0.5" y="0.5" width="7" height="9" stroke="#fff" fill="none"/><path d="M2.5 3H5.5M2.5 5H5.5M2.5 7H5.5" stroke="#fff"/></svg>Business
      <svg width="4" height="4" viewBox="0 0 10 10"><path d="M2 3.5 L5 6.5 L8 3.5" stroke="#fff" stroke-width="1.5" fill="none"/></svg>
    </div>
  </aside>

  <header class="topbar">
    <svg class="abs" style="left:281px;top:14px" width="6" height="6.5" viewBox="0 0 10 11"><path d="M5 0.5 C2.5 0.5 2 2.5 2 4.5 V7 L0.5 8.5 H9.5 L8 7 V4.5 C8 2.5 7.5 0.5 5 0.5 Z" fill="#111"/><circle cx="5" cy="9.8" r="1.1" fill="#111"/></svg>
    <svg class="abs" style="left:297px;top:14px" width="6" height="6" viewBox="0 0 10 10"><circle cx="5" cy="5" r="3.3" stroke="#111" stroke-width="2.2" stroke-dasharray="1.6 1" fill="none"/><circle cx="5" cy="5" r="1.2" fill="#111"/></svg>
    <div class="avatar" role="img" aria-label="User profile photo"></div>
    <div class="search">Search<svg width="5" height="5" viewBox="0 0 10 10"><circle cx="4" cy="4" r="3" stroke="#111" stroke-width="1.5" fill="none"/><path d="M6.3 6.3 L9 9" stroke="#111" stroke-width="1.6"/></svg></div>
  </header>

  <div class="abs crumb" style="left:132px;top:41.5px">Short Term Memory</div>
  <svg class="abs" style="left:218.5px;top:43.5px" width="4" height="4" viewBox="0 0 10 10"><path d="M3.5 2 L6.5 5 L3.5 8" stroke="#1d2b3a" stroke-width="1.4" fill="none"/></svg>
  <div class="abs crumb-leaf" style="left:228px;top:43px">Grab</div>
  <div class="abs subtitle" style="left:132px;top:56px">Here Your Progress So Far</div>
  <div class="abs section-title" style="left:131.5px;top:78.5px">Word Progress</div>

  <div class="step-line" style="left:141px;width:355px"></div>
  <div class="step step--done" style="left:131.5px;top:100px"><svg width="5" height="5" viewBox="0 0 10 10"><path d="M2 5.2 L4.2 7.3 L8 3" stroke="#fff" stroke-width="1.8" fill="none"/></svg></div>
  <div class="step step--current" style="left:253px;top:100px">2</div>
  <div class="step step--todo" style="left:375px;top:100px">3</div>
  <div class="step step--todo" style="left:496px;top:100px">4</div>
  <div class="abs step-label" style="left:126px;top:169.5px;top:169px;display:none"></div>
  <div class="abs step-label" style="left:126px;top:169px;top:169px"></div>
  <div class="abs step-label" style="left:126px;top:110px">Review 1</div>
  <div class="abs step-label" style="left:247px;top:110px">Review 2</div>
  <div class="abs step-label" style="left:369.5px;top:110px">Review 3</div>
  <div class="abs step-label" style="left:490.5px;top:110px">Review 4</div>

  <div class="card card--due" style="left:130px"><h3>Short Term Memory</h3><p>Due</p></div>
  <div class="card card--working" style="left:263px"><h3>Working Memory</h3><p>Go to 5</p></div>
  <div class="card card--long" style="left:396px"><h3>Long Term Memory</h3><p>Go to 5</p></div>

  <p class="body-copy" style="top:168.5px">The word "grab" is most commonly used as a verb, meaning to take something quickly or suddenly. Imagine you're running late for school. You don't have time for breakfast, so you quickly grab an apple from the kitchen and rush out the door. As you reach the bus stop, your friend waves and says, "Hey! Let's grab a coffee after class. Later, when you sit down, your phone starts ringing. You grab it from your bag and answer</p>

  <svg class="chart" viewBox="0 0 824 228" preserveAspectRatio="none">
    <defs><linearGradient id="plotA" x1="0" x2="1"><stop offset="0" stop-color="#dfeafa"/><stop offset="1" stop-color="#ffffff"/></linearGradient></defs>
    <text x="52" y="27" font-family="Poppins,sans-serif" font-size="11" fill="#1d2b3a">Learning Curve Graph</text>
    <rect x="50" y="47" width="774" height="132" fill="url(#plotA)"/>
    <rect x="50" y="47" width="774" height="43" fill="#e3ecfa" opacity="0.6"/>
    <g font-family="Poppins,sans-serif" font-size="7.5" fill="#1d2b3a" text-anchor="end"><text x="41" y="50">120</text><text x="39" y="93">80</text><text x="39" y="136">40</text><text x="35" y="179">0</text></g>
    <rect x="78" y="103" width="32" height="76" fill="#0f2f4f"/>
    <rect x="292" y="74" width="32" height="105" fill="#061523"/>
    <text x="308" y="62" font-family="Poppins,sans-serif" font-size="4.5" fill="#1d2b3a" text-anchor="middle">Rev 1</text>
    <path d="M110 107 C170 115 195 150 220 170 C235 178 260 179 292 179" stroke="#555" stroke-dasharray="1.5 1.5" fill="none"/>
    <path d="M324 78 C400 82 430 120 460 160 C475 178 510 179 540 179" stroke="#555" stroke-dasharray="1.5 1.5" fill="none"/>
    <line x1="50" y1="179" x2="824" y2="179" stroke="#9aa6b2" stroke-width="1"/>
    <g stroke="#9aa6b2"><line x1="95" y1="179" x2="95" y2="190"/><line x1="156" y1="179" x2="156" y2="190"/><line x1="217" y1="179" x2="217" y2="190"/><line x1="278" y1="179" x2="278" y2="190"/><line x1="339" y1="179" x2="339" y2="190"/><line x1="400" y1="179" x2="400" y2="190"/><line x1="461" y1="179" x2="461" y2="190"/><line x1="522" y1="179" x2="522" y2="190"/><line x1="583" y1="179" x2="583" y2="190"/><line x1="644" y1="179" x2="644" y2="190"/><line x1="705" y1="179" x2="705" y2="190"/><line x1="766" y1="179" x2="766" y2="190"/></g>
    <g font-family="Poppins,sans-serif" font-size="5" fill="#1d2b3a" text-anchor="middle"><text x="60" y="198">May 17</text><text x="121" y="198">May 18</text><text x="182" y="198">May 19</text><text x="243" y="198">May 20</text><text x="303" y="198">May 21</text><text x="365" y="198">May 22</text><text x="426" y="198">May 23</text><text x="487" y="198">May 24</text><text x="547" y="198">May 25</text><text x="608" y="198">May 26</text><text x="669" y="198">May 27</text><text x="730" y="198">May 28</text><text x="790" y="198">May 29</text></g>
    <text x="17" y="199" font-family="Poppins,sans-serif" font-size="7.5" fill="#1d2b3a">From</text>
  </svg>

  <div class="abs analysis-title" style="left:132px;top:326px">Word Coach Learning Analysis</div>
  <p class="body-copy" style="top:336.5px">The word "grab" is most commonly used as a verb, meaning to take something quickly or suddenly. Imagine you're running late for school. You don't have time for breakfast, so you quickly grab an apple from the kitchen and rush out the door.</p>
</section>

<!-- Dashboard with vocabulary popup -->
<section class="screen screen--modal">
  <aside class="sidebar">
    <div class="abs brand">QuillVane</div>
    <div class="abs nav-group" style="left:17px;top:42.8px">Word Coach</div>
    <div class="pill" style="left:92px;top:42px;width:15px;height:8.4px">All</div>
    <div class="abs nav-item" style="left:17px;top:63.5px">Short Term Memory</div>
    <div class="abs nav-item" style="left:25px;top:73.8px">Grab</div>
    <div class="abs nav-item" style="left:17px;top:92.8px">Working Memory</div>
    <div class="abs nav-item" style="left:17px;top:111px">Long term Memory</div>
    <div class="abs nav-group" style="left:17px;top:134.8px">Daily English</div>
    <div class="abs nav-group" style="left:17px;top:159px">Business</div>
  </aside>
  <div class="sidebar-veil"></div>
  <header class="topbar">
    <div class="avatar" role="img" aria-label="User profile photo"></div>
    <div class="search">Search</div>
  </header>
  <div class="abs crumb" style="left:132px;top:41.5px">Short Term Memory</div>
  <div class="abs crumb-leaf" style="left:228px;top:43px">Grab</div>
  <div class="card card--working" style="left:396px;background:#b9c3cd"></div>
  <svg class="chart" viewBox="0 0 824 228" preserveAspectRatio="none">
    <text x="52" y="27" font-family="Poppins,sans-serif" font-size="11" fill="#1d2b3a">Learning Curve Graph</text>
    <rect x="50" y="47" width="774" height="132" fill="#e9f0fa"/>
    <rect x="78" y="103" width="32" height="76" fill="#0f2f4f"/>
    <rect x="292" y="74" width="32" height="105" fill="#061523"/>
    <path d="M110 107 C170 115 195 150 220 170 C235 178 260 179 292 179" stroke="#555" stroke-dasharray="1.5 1.5" fill="none"/>
    <path d="M324 78 C400 82 430 120 460 160 C475 178 510 179 540 179" stroke="#555" stroke-dasharray="1.5 1.5" fill="none"/>
    <line x1="50" y1="179" x2="824" y2="179" stroke="#9aa6b2"/>
  </svg>
  <div class="abs analysis-title" style="left:132px;top:326px">Word Coach Learning Analysis</div>
  <p class="body-copy" style="top:336.5px">The word "grab" is most commonly used as a verb, meaning to take something quickly or suddenly. Imagine you're running late for school. You don't have time for breakfast, so you quickly grab an apple from the kitchen and rush out the door.</p>
  <div class="veil"></div>

  <div class="vocab-popup">
    <div class="pill pill--dark" style="left:10.7px;top:8.4px;width:15.5px;height:9px">All<svg width="3" height="3" viewBox="0 0 10 10"><path d="M2 3.5 L5 6.5 L8 3.5" stroke="#fff" stroke-width="1.5" fill="none"/></svg></div>
    <div class="close"><svg width="8" height="8" viewBox="0 0 10 10"><path d="M3.2 3.2 L6.8 6.8 M6.8 3.2 L3.2 6.8" stroke="#fff" stroke-width="1.3"/></svg></div>
    <div class="chip" style="top:28px">Short Term Memory</div>
    <div class="abs word" style="left:13.5px;top:51.5px">Grab</div>
    <div class="chip" style="top:67px">Working Memory</div>
    <div class="abs word" style="left:13.5px;top:90px">Cool Down</div>
    <div class="abs word" style="left:58.7px;top:90px">Crave</div>
    <div class="abs word" style="left:91.8px;top:90px">Go For</div>
    <div class="abs word" style="left:125.3px;top:90px">Go To</div>
    <div class="abs word" style="left:157px;top:90px">In The Mood For</div>
    <div class="abs word" style="left:216px;top:90px">Sip</div>
    <div class="abs word" style="left:241px;top:90px">Smoothing</div>
    <div class="abs word" style="left:287px;top:90px">Stick With</div>
    <div class="abs word" style="left:330px;top:90px">Throw In / Throw On</div>
    <div class="chip" style="top:108px">Long Term Memory</div>
    <div class="abs word" style="left:13.5px;top:131.5px">Give it Away</div>
  </div>
</section>

</body>
</html>
```